Marine Services Letterhead design

We need a letterhead design for an Australian owned company in Victoria named K+T Harbour Works Pty Ltd. We provide linesmen and launches to assist the large ships that come into port.
Our colour is orange.
The final design should have a strong nautical theme and communicate safety and reliability.
I would like to use the letter head on invoices so it should print to pdf well.

Target Market(s)

Owners and representatives of shipping companies. It is not for general public

Industry/Entity Type

Nautical

Requirements
Must have
• A shipping theme, not overly complicated, featuring safety orange colours but not all orange of course.
The letterhead should just sit at the top of the page so I can use for invoices.
Nice to have
• Something elegant and stylish
Should not have
• cartoons or pop art

```html
<!DOCTYPE html>
<html lang="en">
<head>
<meta charset="utf-8">
<title>K+T Harbour Works Pty Ltd – Letterhead</title>
<link rel="stylesheet" href="https://fonts.googleapis.com/css2?family=Marcellus+SC&family=Source+Sans+3:wght@400&display=swap">
<style>
  :root {
    --page: #ffffff;
    --ink: #1f1f1f;
    --band: #92c5a2;
    --brand-orange: #e8b36a;
    --footer-ink: #1e2a22;
    --badge: #ffffff;
  }
  * { margin: 0; padding: 0; box-sizing: border-box; }
  html, body {
    width: 883px;
    height: 1200px;
    overflow: hidden;
    background: var(--page);
  }
  .letterhead {
    position: relative;
    width: 883px;
    height: 1200px;
    background: var(--page);
  }
  .brand-mark {
    position: absolute;
    left: 65px;
    top: 40px;
    width: 160px;
    height: 156px;
    background: var(--brand-orange);
    display: flex;
    align-items: center;
    justify-content: center;
    font-family: "Marcellus SC", serif;
    font-size: 46px;
    color: var(--ink);
  }
  .company-name {
    position: absolute;
    right: 43px;
    top: 103px;
    font-family: "Marcellus SC", serif;
    font-weight: 400;
    font-size: 24px;
    letter-spacing: 0.4px;
    color: var(--ink);
  }
  .footer-band {
    position: absolute;
    left: 0;
    bottom: 0;
    width: 100%;
    height: 79px;
    background: var(--band);
    display: flex;
    align-items: center;
    padding-left: 63px;
    font-family: "Source Sans 3", sans-serif;
    font-size: 16px;
    color: var(--footer-ink);
  }
  .contact-item {
    display: flex;
    align-items: center;
    gap: 3px;
    margin-right: 10px;
  }
  .contact-item svg { width: 11px; height: 14px; fill: var(--footer-ink); }
  .divider {
    width: 1.5px;
    height: 26px;
    background: var(--footer-ink);
    margin: 0 12px 0 2px;
  }
  .footer-badge {
    position: absolute;
    left: 736px;
    bottom: 6px;
    width: 66px;
    height: 66px;
    border-radius: 50%;
    background: var(--badge);
  }
</style>
</head>
<body>
  <main class="letterhead">
    <header>
      <div class="brand-mark">K+T</div>
      <h1 class="company-name">K+T Harbour Works Pty Ltd</h1>
    </header>

    <footer class="footer-band">
      <span class="contact-item">
        <svg viewBox="0 0 11 14" aria-hidden="true"><path d="M3 0.5 L4.6 3.6 L3.4 4.8 C3.6 7 4.6 8.8 6.4 10 L7.8 9 L10.5 11.5 L8.8 13.5 C4 12.5 0.8 7.5 1 2 Z"/></svg>
        1300 555 018
      </span>
      <span class="contact-item">
        <svg viewBox="0 0 11 14" aria-hidden="true"><path d="M5.5 0 C2.5 0 0.5 2.2 0.5 5 C0.5 8.5 5.5 14 5.5 14 C5.5 14 10.5 8.5 10.5 5 C10.5 2.2 8.5 0 5.5 0 Z M5.5 7 A2 2 0 1 1 5.5 3 A2 2 0 1 1 5.5 7 Z"/></svg>
        PO Box 214 Seaview 3999
      </span>
      <span class="divider"></span>
      <span class="contact-item">ABN: 12345678901</span>
      <span class="footer-badge" aria-hidden="true"></span>
    </footer>
  </main>
</body>
</html>
```